Phuket Thailand - Rental Villa Website

I have a villa for rent in Thailand and require a website - i need to demo pictures/walk through video, local attractions, villa facilities description plus seaonal rates and online booking.

Industry/Entity Type

Rental

Coding

Coded - Design and coding required

```html
<!DOCTYPE html>
<html lang="en">
<head>
<meta charset="utf-8">
<title>Villa Rental – Phuket, Thailand</title>
<link href="https://fonts.googleapis.com/css2?family=Mulish:wght@300;400;500;600;700&display=swap" rel="stylesheet">
<style>
:root{
  --blue:#1b8de2;
  --blue-text:#1a86d8;
  --orange:#f7870f;
  --dark:#2a2a2a;
  --ink:#333333;
  --muted:#6b6b6b;
  --band:#f1f1f1;
  --line:#dcdcdc;
  --footer:#333333;
  --white:#ffffff;
}
*{box-sizing:border-box;margin:0;padding:0}
html,body{width:1200px;height:2192px;overflow:hidden;background:var(--white)}
body{font-family:"Mulish",Arial,sans-serif;color:var(--ink);position:relative}
.abs{position:absolute}
.btn{position:absolute;background:var(--orange);color:var(--white);font-size:13px;font-weight:500;text-transform:uppercase;display:flex;align-items:center;justify-content:center;letter-spacing:.3px}
.btn-dark{background:var(--dark)}
.section-title{position:absolute;color:var(--blue-text);font-size:22px;font-weight:400;text-transform:uppercase;letter-spacing:.3px}
.body-text{position:absolute;font-size:11.5px;line-height:21px;color:var(--ink)}
.band{position:absolute;left:0;width:1200px;background:var(--band)}
.photo{position:absolute}

/* header */
.logo{left:75px;top:22px;font-size:42px;font-weight:400;color:#222;letter-spacing:.5px}
.top-links{right:75px;top:18px;font-size:11.5px;color:#555;display:flex;gap:8px}
.top-links span.sep{color:#999}
.phone{left:694px;top:52px;font-size:16px;color:#222;display:flex;align-items:center;gap:10px}
.search{left:924px;top:48px;width:201px;height:31px;border:1px solid #d8d8d8;background:#f4f4f4}
.search span{position:absolute;left:12px;top:8px;font-size:11px;font-style:italic;color:#999}
.search .go{position:absolute;right:-1px;top:-1px;width:36px;height:31px;background:var(--orange);display:flex;align-items:center;justify-content:center}
.nav{left:75px;top:91px;width:1050px;height:39px;background:var(--blue);display:flex;align-items:center;justify-content:space-around;padding:0 8px}
.nav a{color:var(--white);text-decoration:none;font-size:13px;text-transform:uppercase}

/* hero */
.hero{left:77px;top:136px;width:1046px;height:390px;background:linear-gradient(180deg,#5a7fb8 0%,#8ea3c6 30%,#6b5f63 55%,#a8a3a8 75%,#2f67c9 100%);border:2px solid #d9d9d9}
.hero-title{left:78px;top:234px;width:561px;height:134px;background:rgba(20,30,45,.72);color:var(--white);font-size:47px;line-height:68px;padding:0 0 0 36px}
.hero .dots{position:absolute;left:36px;top:346px;display:flex;gap:6px}
.dots i{display:block;width:16px;height:16px;border-radius:50%;background:#111}
.dots i:first-child{background:var(--orange)}

/* booking form */
.booking{left:794px;top:576px;width:331px;height:386px;background:var(--orange)}
.booking h2{position:absolute;left:19px;top:22px;color:var(--white);font-size:23px;font-weight:400;text-transform:uppercase;letter-spacing:.3px}
.field{position:absolute;height:34px;background:var(--white);border:1px solid #e3e3e3;font-size:11.5px;font-style:italic;color:#777;padding:0 12px;display:flex;align-items:center;justify-content:space-between}

/* cards */
.card{position:absolute;top:1052px;width:242px;height:315px;background:var(--white);border:1px solid #e2e2e2}
.card .photo{left:13px;top:13px;width:216px;height:147px}
.card h3{position:absolute;left:13px;top:175px;font-size:13px;font-weight:500;color:var(--blue-text);text-transform:uppercase}
.card p{position:absolute;left:13px;top:195px;width:218px;font-size:11.5px;line-height:18.5px}
.card .price{position:absolute;left:19px;top:270px;font-size:19px;color:#222}
.card .btn{left:107px;top:262px;width:117px;height:34px}

.rate{position:absolute;top:1739px;width:242px}
.rate .photo{left:0;top:0;width:242px;height:132px}
.rate h4{position:absolute;top:143px;font-size:14px;font-weight:500;color:#222}
.rate .price{position:absolute;top:170px;font-size:13.5px;white-space:nowrap}
.rate .old{text-decoration:line-through;color:#555}
.rate .new{color:var(--blue-text)}

/* footer */
.footer{left:0;top:2075px;width:1200px;height:117px;background:var(--footer)}
.footer small{position:absolute;left:75px;font-size:11px;font-style:italic;color:#aaa}
.footer h5{position:absolute;top:26px;font-size:16px;font-weight:400;color:#ddd}
.social{position:absolute;left:697px;top:60px;display:flex;gap:8px}
.social span{font-size:11px;color:var(--white);display:flex;align-items:center;gap:4px}
.social span::before{content:"";width:8px;height:8px;border-radius:50%;background:var(--white)}
.cards{position:absolute;left:903px;top:60px;display:flex;gap:5px}
.cards span{background:var(--white);color:#333;font-size:9.5px;font-weight:600;padding:6px 4px}
</style>
</head>
<body>

<header>
  <div class="abs logo">Villa Rental</div>
  <nav class="abs top-links"><span>Log In</span><span class="sep">|</span><span>Register</span><span class="sep">|</span><span>FAQ</span><span class="sep">|</span><span>SiteMap</span></nav>
  <div class="abs phone">
    <svg width="17" height="17" viewBox="0 0 17 17"><rect width="17" height="17" rx="3" fill="#333"/><path d="M5 4c1 0 1.5 2 1.3 2.6L5.6 7.3c.6 1.5 2 2.9 3.5 3.5l.7-.7c.6-.2 2.6.3 2.6 1.3 0 1-1 2-2 2C7 13.4 3.6 10 3.6 6 3.6 5 4 4 5 4z" fill="#fff"/></svg>
    <span>CALL US: <b style="font-weight:600">123-456-7890</b></span>
  </div>
  <div class="abs search"><span>Search..</span>
    <div class="go"><svg width="16" height="16" viewBox="0 0 16 16"><circle cx="6.5" cy="6.5" r="4.5" stroke="#fff" stroke-width="2" fill="none"/><line x1="10" y1="10" x2="14.5" y2="14.5" stroke="#fff" stroke-width="2.4"/></svg></div>
  </div>
  <nav class="abs nav">
    <a>Home</a><a>About Us</a><a>Services</a><a>Online Booking</a><a>Rates</a><a>Latest News</a><a>Gallery</a><a>Blog</a><a>Location</a><a>Contact Us</a>
  </nav>
</header>

<section class="abs hero" role="img" aria-label="Villa terrace with infinity pool at dusk">
  <div class="dots"><i></i><i></i><i></i><i></i></div>
</section>
<h1 class="abs hero-title" style="font-weight:400">Villa Rental Service in Phuket, Thailand</h1>
<div class="btn" style="left:115px;top:373px;width:157px;height:44px;font-size:18px">Book Now</div>

<section class="welcome">
  <h2 class="section-title" style="left:75px;top:568px">Welcome to our website</h2>
  <p class="body-text" style="left:75px;top:606px;width:670px">Aliquam molestie, mi et imperdiet euismod, dui purus auctor tellus, et interdum lacus lectus et ante. Sed accumsan sollicitudin sapien, sit amet adipiscing turpis gravida ac. In congue, neque ac lobortis volutpat, libero mauris varius mi, vitae suscipit ipsum ligula vitae risus. Duis aliquam nibh a dui iaculis viverra id a velit. Vivamus egestas risus in magna varius commodo. Sed semper viverra egestas. Etiam pretium porttitor lectus, vel ornare neque porta volutpat.</p>
  <div class="btn" style="left:75px;top:713px;width:116px;height:35px">Read More</div>
  <div class="abs" style="left:75px;top:770px;width:669px;height:1px;background:var(--line)"></div>

  <h2 class="section-title" style="left:75px;top:793px">Watch a video</h2>
  <p class="body-text" style="left:75px;top:827px;width:320px">Aliquam molestie, mi et imperdiet euismod, dui purus auctor tellus, et interdum lacus lectus et ante. Sed accumsan sollicitudin sapien, sit amet adipiscing turpis gravida ac.</p>
  <div class="btn" style="left:75px;top:925px;width:116px;height:37px">More Video</div>
  <div class="photo" role="img" aria-label="Video thumbnail: aerial view of the bay and resort pool" style="left:434px;top:797px;width:311px;height:165px;background:linear-gradient(180deg,#6f8d9d 0%,#4f7a63 45%,#5f7a52 70%,#3f7fa6 100%);border:1px solid #ccc;display:flex;align-items:center;justify-content:center">
    <svg width="50" height="50" viewBox="0 0 50 50"><circle cx="25" cy="25" r="22" fill="rgba(0,0,0,.25)" stroke="#fff" stroke-width="3"/><path d="M20 15l14 10-14 10z" fill="#fff"/></svg>
  </div>
</section>

<form class="abs booking">
  <h2>Online Booking</h2>
  <div class="field" style="left:20px;top:64px;width:291px">Your Name</div>
  <div class="field" style="left:20px;top:108px;width:142px">Check in Date<svg width="20" height="16" viewBox="0 0 20 16"><rect x="1" y="2" width="18" height="13" fill="none" stroke="#888"/><rect x="1" y="2" width="18" height="3" fill="#888"/><path d="M4 8h12M4 11h12M7 6v9M10 6v9M13 6v9" stroke="#aaa"/></svg></div>
  <div class="field" style="left:169px;top:108px;width:142px">Checkout Date<svg width="20" height="16" viewBox="0 0 20 16"><rect x="1" y="2" width="18" height="13" fill="none" stroke="#888"/><rect x="1" y="2" width="18" height="3" fill="#888"/><path d="M4 8h12M4 11h12M7 6v9M10 6v9M13 6v9" stroke="#aaa"/></svg></div>
  <div class="field" style="left:20px;top:150px;width:142px">No. of adults<svg width="10" height="6"><path d="M0 0h10L5 6z" fill="#999"/></svg></div>
  <div class="field" style="left:169px;top:150px;width:142px">No.of room<svg width="10" height="6"><path d="M0 0h10L5 6z" fill="#999"/></svg></div>
  <div class="field" style="left:20px;top:193px;width:291px">Email Address</div>
  <div class="field" style="left:20px;top:235px;width:142px">Contact No</div>
  <div class="field" style="left:169px;top:235px;width:142px">Location<svg width="10" height="6"><path d="M0 0h10L5 6z" fill="#999"/></svg></div>
  <div class="field" style="left:20px;top:278px;width:291px">Choose Packages<svg width="10" height="6"><path d="M0 0h10L5 6z" fill="#999"/></svg></div>
  <div class="btn btn-dark" style="left:160px;top:329px;width:151px;height:41px;font-size:16px">Book Now</div>
</form>

<section class="band" style="top:990px;height:409px"></section>
<h2 class="section-title" style="left:75px;top:1011px">Local Attractions</h2>
<article class="card" style="left:75px"><div class="photo" role="img" aria-label="Villa exterior with tiled roof" style="background:linear-gradient(160deg,#c9d3d9,#5a5048 55%,#3f4d33)"></div><h3>Lorem Ipsum Dolor</h3><p>Aliquam molestie, mi et imperdiet euismod, dui purus auctor tellus, et interdum lacus lectus et ante.</p><span class="price">$ 1, 120</span><div class="btn">Book Now</div></article>
<article class="card" style="left:343px"><div class="photo" role="img" aria-label="Bedroom interior" style="background:linear-gradient(160deg,#3a2f28,#8a7c70 55%,#c8c4c0)"></div><h3>Lorem Ipsum Dolor</h3><p>Aliquam molestie, mi et imperdiet euismod, dui purus auctor tellus, et interdum lacus lectus et ante.</p><span class="price">$ 1, 120</span><div class="btn">Book Now</div></article>
<article class="card" style="left:614px"><div class="photo" role="img" aria-label="Pool deck pavilion facing the hills" style="background:linear-gradient(180deg,#8aa0a8,#3f5a3a 45%,#b6b4ae)"></div><h3>Lorem Ipsum Dolor</h3><p>Aliquam molestie, mi et imperdiet euismod, dui purus auctor tellus, et interdum lacus lectus et ante.</p><span class="price">$ 1, 120</span><div class="btn">Book Now</div></article>
<article class="card" style="left:883px"><div class="photo" role="img" aria-label="Thai-style villa among palm trees" style="background:linear-gradient(180deg,#a9c2d8,#8a4a32 50%,#4d6a3a)"></div><h3>Lorem Ipsum Dolor</h3><p>Aliquam molestie, mi et imperdiet euismod, dui purus auctor tellus, et interdum lacus lectus et ante.</p><span class="price">$ 1, 120</span><div class="btn">Book Now</div></article>

<section class="facilities">
  <div class="photo" role="img" aria-label="Thai pavilion over a pool surrounded by palms" style="left:75px;top:1437px;width:330px;height:197px;background:linear-gradient(180deg,#7fa6cf 0%,#5a6a45 40%,#2e4a2a 65%,#0f2d6a 100%)"></div>
  <h2 class="section-title" style="left:434px;top:1432px">Villa Facilities</h2>
  <p class="body-text" style="left:434px;top:1469px;width:690px;line-height:22px">Aliquam molestie, mi et imperdiet euismod, dui purus auctor tellus, et interdum lacus lectus et ante. Sed accumsan sollicitudin sapien, sit amet adipiscing turpis gravida ac. In congue, neque ac lobortis volutpat, libero mauris varius mi, vitae suscipit ipsum ligula vitae risus. Duis aliquam nibh a dui iaculis viverra id a velit. Vivamus egestas risus in magna varius commodo. Sed semper viverra egestas. Etiam pretium porttitor lectus, vel ornare neque porta volutpat.</p>
  <div class="btn" style="left:434px;top:1599px;width:117px;height:35px">Book Now</div>
</section>

<section class="band" style="top:1663px;height:303px"></section>
<h2 class="section-title" style="left:75px;top:1692px">Seasonal Rates</h2>
<article class="rate" style="left:75px"><div class="photo" role="img" aria-label="Open-air pavilion beside a pool" style="background:linear-gradient(160deg,#e8e2d6,#7a6a55 45%,#2f86b0)"></div><h4>Heading Title</h4><p class="price"><span class="old">$1500.00</span> &nbsp;|&nbsp; <span class="new">$1000.00</span></p></article>
<article class="rate" style="left:343px"><div class="photo" role="img" aria-label="Resort lit at night" style="background:linear-gradient(180deg,#2a4c86,#3a3046 50%,#c58a4a)"></div><h4>Heading Title</h4><p class="price"><span class="old">$1500.00</span> &nbsp;|&nbsp; <span class="new">$1000.00</span></p></article>
<article class="rate" style="left:615px"><div class="photo" role="img" aria-label="Thai villa rooftops" style="background:linear-gradient(180deg,#b9cde0,#6a3a2a 55%,#4a5a3a)"></div><h4>Heading Title</h4><p class="price"><span class="old">$1500.00</span> &nbsp;|&nbsp; <span class="new">$1000.00</span></p></article>
<article class="rate" style="left:884px"><div class="photo" role="img" aria-label="Red-roofed villas with pool" style="background:linear-gradient(180deg,#c6d8e6,#8a3a2e 50%,#3f7a5a)"></div><h4>Heading Title</h4><p class="price"><span class="old">$1500.00</span> &nbsp;|&nbsp; <span class="new">$1000.00</span></p></article>

<section class="newsletter">
  <h2 class="section-title" style="left:75px;top:2011px">Newsletter Subscribe</h2>
  <div class="abs" style="left:370px;top:1998px;width:755px;height:54px;border:1px solid #cfcfcf;background:var(--white)">
    <span class="abs" style="left:20px;top:18px;font-size:12.5px;font-style:italic;color:#888">Enter Email Address</span>
  </div>
  <div class="btn btn-dark" style="left:957px;top:2007px;width:158px;height:38px;font-size:16px">Subscribe</div>
</section>

<footer class="abs footer">
  <small style="top:42px">Copyright © 2015.Comapny Name All Right Reserved</small>
  <small style="top:62px">Privacy Policy &nbsp;|&nbsp; Term of Services</small>
  <h5 style="left:697px">Connect Us</h5>
  <div class="social"><span>Kestrel</span><span>Harbor</span><span>Lumen</span><span>Orbit</span><span>Reel</span></div>
  <h5 style="left:903px">We Accept</h5>
  <div class="cards"><span>PayWise</span><span>Vantage</span><span>Meridian</span><span>Atlas</span><span>Compass</span></div>
</footer>

</body>
</html>
```